Movie Poster - Beneath Pale Iron Skies

Documentary-film poster design.
Attached is a PDF brief with information on what is required and examples of poster designs I like.

The project is a true crime / mystery documentary film. Set in the Soviet Union in 1959.

Colors
3276b5
85abd2
ec1f27

```html
<!DOCTYPE html>
<html lang="en">
<head>
<meta charset="utf-8">
<title>Beneath Pale Iron Skies — Poster</title>
<link rel="stylesheet" href="https://fonts.googleapis.com/css2?family=Bebas+Neue&family=Montserrat:wght@300;400&display=swap">
<style>
  :root {
    --ink: #0d0d0d;
    --charcoal: #1c1c1c;
    --frost: #f6f4f4;
    --signal-red: #ec1f27;
    --steel-blue: #3276b5;
    --ice-blue: #85abd2;
    --white: #ffffff;
  }
  * { margin: 0; padding: 0; box-sizing: border-box; }
  html, body { width: 927px; height: 1200px; overflow: hidden; background: var(--ink); }
  .poster {
    position: relative;
    width: 927px;
    height: 1200px;
    overflow: hidden;
    background: var(--charcoal);
    font-family: "Montserrat", sans-serif;
  }
  .poster__backdrop { position: absolute; inset: 0; }
  .title { position: absolute; left: 0; right: 0; text-align: center; display: block; }
  .title__lead {
    top: 294px;
    font-weight: 400;
    font-size: 50px;
    letter-spacing: 1px;
    color: var(--signal-red);
    text-shadow: 0 0 8px rgba(255,255,255,0.55);
    line-height: 1;
  }
  .title__main {
    top: 352px;
    left: 4px;
    font-family: "Bebas Neue", sans-serif;
    font-weight: 400;
    font-size: 122px;
    letter-spacing: 4px;
    color: var(--ink);
    line-height: 1;
    text-shadow: 0 0 4px rgba(255,255,255,0.35);
  }
  .subtitle {
    position: absolute;
    top: 743px;
    left: 0; right: 0;
    text-align: center;
    font-weight: 300;
    font-size: 22px;
    letter-spacing: 0.6px;
    color: var(--ink);
  }
  .subtitle__place { color: var(--white); text-shadow: 0 0 3px rgba(0,0,0,0.45); }
  .taglines {
    position: absolute;
    top: 830px;
    left: 0; right: 0;
    text-align: center;
    list-style: none;
    color: var(--signal-red);
    font-weight: 400;
    font-size: 15px;
    letter-spacing: 0.8px;
    line-height: 27.5px;
  }
</style>
</head>
<body>
<main class="poster">
  <svg class="poster__backdrop" width="927" height="1200" viewBox="0 0 927 1200">
    <defs>
      <radialGradient id="glow-top" cx="0.6" cy="0.04" r="0.5">
        <stop offset="0" stop-color="#f4f4f4"/>
        <stop offset="0.5" stop-color="#c4c6c9"/>
        <stop offset="1" stop-color="#1c1c1c" stop-opacity="0"/>
      </radialGradient>
      <radialGradient id="glow-mid" cx="0.5" cy="0.5" r="0.5">
        <stop offset="0" stop-color="#ffffff"/>
        <stop offset="0.55" stop-color="#e2e2e2"/>
        <stop offset="1" stop-color="#1c1c1c" stop-opacity="0"/>
      </radialGradient>
      <radialGradient id="glow-right" cx="0.5" cy="0.5" r="0.5">
        <stop offset="0" stop-color="#8a8a8a"/>
        <stop offset="1" stop-color="#1c1c1c" stop-opacity="0"/>
      </radialGradient>
      <linearGradient id="cold-wash" x1="0" y1="0" x2="1" y2="1">
        <stop offset="0" stop-color="#3276b5" stop-opacity="0.16"/>
        <stop offset="0.5" stop-color="#85abd2" stop-opacity="0.06"/>
        <stop offset="1" stop-color="#3276b5" stop-opacity="0.18"/>
      </linearGradient>
      <linearGradient id="scene-tone" x1="0" y1="0" x2="1" y2="0">
        <stop offset="0" stop-color="#ec1f27"/>
        <stop offset="0.1" stop-color="#ee4b51"/>
        <stop offset="0.2" stop-color="#f7c8ca"/>
        <stop offset="0.3" stop-color="#fbe9ea"/>
        <stop offset="0.37" stop-color="#ee5258"/>
        <stop offset="0.5" stop-color="#ec3a41"/>
        <stop offset="0.58" stop-color="#f4a9ac"/>
        <stop offset="0.66" stop-color="#ee4e54"/>
        <stop offset="0.78" stop-color="#f07a7f"/>
        <stop offset="0.88" stop-color="#ec3037"/>
        <stop offset="1" stop-color="#ec1f27"/>
      </linearGradient>
      <linearGradient id="scene-fade" x1="0" y1="0" x2="0" y2="1">
        <stop offset="0" stop-color="#fbf7f7" stop-opacity="1"/>
        <stop offset="0.25" stop-color="#fbf7f7" stop-opacity="0.55"/>
        <stop offset="0.6" stop-color="#ffffff" stop-opacity="0.1"/>
        <stop offset="0.85" stop-color="#ffffff" stop-opacity="0.35"/>
        <stop offset="1" stop-color="#ffffff" stop-opacity="0"/>
      </linearGradient>
      <linearGradient id="scene-shade" x1="0" y1="0" x2="0" y2="1">
        <stop offset="0" stop-color="#85abd2" stop-opacity="0.12"/>
        <stop offset="1" stop-color="#3276b5" stop-opacity="0.05"/>
      </linearGradient>
      <filter id="film-grain" x="0" y="0" width="100%" height="100%">
        <feTurbulence type="fractalNoise" baseFrequency="0.85" numOctaves="2" seed="7" result="noise"/>
        <feColorMatrix in="noise" type="saturate" values="0"/>
        <feComponentTransfer>
          <feFuncA type="table" tableValues="0 0.18"/>
        </feComponentTransfer>
      </filter>
    </defs>

    <rect class="backdrop__base" width="927" height="1200" fill="#1c1c1c"/>
    <g role="img" aria-label="Grainy dark film photograph with a pale light leak">
      <rect class="backdrop__light" width="927" height="1200" fill="url(#glow-top)"/>
      <ellipse class="backdrop__side-glow" cx="880" cy="690" rx="120" ry="90" fill="url(#glow-right)"/>
      <ellipse class="backdrop__glow" cx="445" cy="735" rx="340" ry="100" fill="url(#glow-mid)"/>
    </g>

    <path class="band band--upper" fill="#101010" opacity="0.72"
      d="M0 258 L180 260 L400 258 L620 262 L800 266 L927 272 L927 420 L600 430 L300 440 L0 448 Z"/>

    <path class="band band--snow" fill="#f6f4f4"
      d="M0 456 L90 452 L120 446 L220 436 L420 432 L640 420 L800 412 L927 410 L927 712 L700 718 L520 726 L330 722 L150 716 L0 712 Z"/>

    <g role="img" aria-label="Red-toned photograph of hooded hikers with rucksacks and ski poles in the snow">
      <path class="band band--scene" fill="url(#scene-tone)"
        d="M0 458 L120 448 L300 440 L480 436 L700 430 L927 424 L927 712 L700 718 L520 726 L330 722 L150 716 L0 712 Z"/>
      <path fill="url(#scene-fade)"
        d="M0 458 L120 448 L300 440 L480 436 L700 430 L927 424 L927 712 L700 718 L520 726 L330 722 L150 716 L0 712 Z"/>
      <path fill="url(#scene-shade)"
        d="M0 458 L120 448 L300 440 L480 436 L700 430 L927 424 L927 712 L700 718 L520 726 L330 722 L150 716 L0 712 Z"/>
    </g>

    <path class="band band--under" fill="#121212"
      d="M0 710 L150 714 L330 720 L520 724 L700 716 L927 708 L927 726 L620 734 L300 732 L0 728 Z"/>

    <path class="band band--lower" fill="#101010" opacity="0.85"
      d="M0 930 L160 928 L380 934 L600 926 L820 920 L927 918 L927 944 L700 950 L420 966 L200 970 L0 966 Z"/>

    <rect class="backdrop__cold" width="927" height="1200" fill="url(#cold-wash)"/>
    <rect class="backdrop__grain" width="927" height="1200" filter="url(#film-grain)"/>
  </svg>

  <h1>
    <span class="title title__lead">BENEATH PALE</span>
    <span class="title title__main">IRON SKIES</span>
  </h1>

  <p class="subtitle">The true story of the <span class="subtitle__place">Veresk Pass Incident</span></p>

  <ul class="taglines">
    <li>Nine dead hikers</li>
    <li>Sixty years of secrets</li>
    <li>Russia’s greatest mystery uncovered.</li>
  </ul>
</main>
</body>
</html>
```